Quorva - corporate Business Card

We need a good look and innovative business card for a new start up company based in Los Angeles called "Quorva". We are in a payment business, including payment card, app, and ewallet. We are expert in online payment and Card not present (CNP) transaction.
We need an innovative, modern business card.

Our logo font is Aero Matics

Target Market(s)

Startup - Bank - Online Payment - Card Manufacturing

Industry/Entity Type

Startup

Contact Information for Business Card

phone: 555 014 7396 - Address: 4172 Marlowe blvd, Brennick Falls, OR 97299

Requirements
Must have
• Message: innovative, professional, expert, high tech, trust, online payment expert, security
Nice to have
• no comment
Should not have
• no Comment

```html
<!DOCTYPE html>
<html lang="en">
<head>
<meta charset="utf-8">
<title>Quorva Business Card</title>
<link rel="stylesheet" href="https://fonts.googleapis.com/css2?family=Exo+2:wght@500&family=Lato:wght@400;700&display=swap">
<style>
  :root {
    --brand-red: #b31e2d;
    --card-white: #f9f9f9;
    --page-bg: #ececec;
    --ink: #1d1d1d;
    --paper-text: #ffffff;
  }
  * { margin: 0; padding: 0; box-sizing: border-box; }
  html, body {
    width: 1200px; height: 586px; overflow: hidden;
    background: var(--page-bg);
    font-family: "Lato", Arial, sans-serif;
  }
  .stage { position: relative; width: 1200px; height: 586px; }
  .card {
    position: absolute; top: 129px; width: 501px; height: 300px; overflow: hidden;
  }
  /* Front side */
  .card-front { left: 61px; background: var(--brand-red); }
  .front-rule {
    position: absolute; left: 250px; width: 3px; background: var(--paper-text);
  }
  .front-rule.upper { top: 0; height: 198px; }
  .front-rule.lower { top: 284px; height: 16px; }
  .front-name {
    position: absolute; left: 0; width: 503px; top: 206px; text-align: center;
    font-family: "Exo 2", Arial, sans-serif; font-weight: 500;
    font-size: 44px; line-height: 1; color: var(--paper-text);
  }
  .front-url {
    position: absolute; left: 0; width: 503px; top: 262px; text-align: center;
    font-weight: 700; font-size: 11.5px; letter-spacing: 3px; color: var(--paper-text);
  }
  /* Back side */
  .card-back { left: 619px; background: var(--card-white); }
  .brand {
    position: absolute; left: 145px; top: 33px; display: flex; align-items: center; gap: 10px;
  }
  .brand-dot { width: 64px; height: 64px; border-radius: 50%; background: var(--brand-red); }
  .brand-name {
    font-family: "Exo 2", Arial, sans-serif; font-weight: 500;
    font-size: 48px; line-height: 1; color: var(--brand-red); margin-top: -6px;
  }
  .person {
    position: absolute; right: 294px; top: 166px; text-align: right;
  }
  .person-name { font-weight: 700; font-size: 16.5px; color: var(--brand-red); }
  .person-role { font-size: 11.5px; color: var(--ink); margin-top: 3px; }
  .info-divider {
    position: absolute; left: 235px; top: 142px; width: 2px; height: 105px;
    background: linear-gradient(to bottom, rgba(179,30,45,0), var(--brand-red) 35%, var(--brand-red) 55%, rgba(179,30,45,0));
  }
  .contacts { position: absolute; left: 261px; top: 166px; list-style: none; }
  .contacts li {
    display: flex; align-items: center; gap: 8px; height: 25px;
    font-size: 12px; color: var(--ink);
  }
  .contact-icon { width: 18px; height: 18px; }
  .address-band {
    position: absolute; left: 0; bottom: 0; width: 100%; height: 30px;
    background: var(--brand-red); color: var(--paper-text);
    font-weight: 700; font-size: 12px; text-align: center; line-height: 30px;
  }
</style>
</head>
<body>
<main class="stage">
  <section class="card card-front" aria-label="Card front">
    <div class="front-rule upper"></div>
    <div class="front-rule lower"></div>
    <p class="front-name">quorva</p>
    <p class="front-url">www.quorvawebsite.com</p>
  </section>

  <section class="card card-back" aria-label="Card back">
    <div class="brand">
      <span class="brand-dot"></span>
      <span class="brand-name">quorva</span>
    </div>

    <div class="person">
      <p class="person-name">Marcus Halden</p>
      <p class="person-role">Owner &amp; Founder</p>
    </div>

    <div class="info-divider"></div>

    <ul class="contacts">
      <li>
        <svg class="contact-icon" viewBox="0 0 18 18" aria-hidden="true">
          <circle cx="9" cy="9" r="9" fill="var(--brand-red)"/>
          <path d="M4.5 7.5 Q9 4 13.5 7.5 L12.5 9 L10.8 8.2 L10.8 7.2 Q9 6.6 7.2 7.2 L7.2 8.2 L5.5 9 Z" fill="#fff"/>
          <rect x="5.8" y="9.4" width="6.4" height="3.6" rx="0.8" fill="#fff"/>
        </svg>
        <span>(555) 014-7396</span>
      </li>
      <li>
        <svg class="contact-icon" viewBox="0 0 18 18" aria-hidden="true">
          <circle cx="9" cy="9" r="9" fill="var(--brand-red)"/>
          <rect x="4.5" y="5.8" width="9" height="6.4" fill="#fff"/>
          <path d="M4.5 5.8 L9 9.6 L13.5 5.8" fill="none" stroke="var(--brand-red)" stroke-width="0.9"/>
        </svg>
        <span>MarcusH@quorvaweb.com</span>
      </li>
    </ul>

    <p class="address-band">4172 Marlowe blvd, Brennick Falls, OR 97299</p>
  </section>
</main>
</body>
</html>
```